Develop website for Cloud Security Startup

Looking for a logo that conveys the outsourced security and management of clients data, systems and development in Tellix, Bri and Pindle with an emphasis on security and compliance

Target Market(s)

Companies looking for professional services IT firm

Coding

Coded - Design and coding required

Number of Pages Required

5+ page

Font styles to use
Sans Serif

Colors
0455a3
33a6d7

Requirements
Must have
• Landing Page
- Help me get started

Move to the cloud safely
- Benefits of Cloud

What we do
- Cloud Adoption
- Managed Services
- Optimise

Resources
- News
- Resources
- Events
- Webinars
- Not for profit
- Case Studies
- Support Button
- Incident Button

Company
- About Us
- Why Vorplexa?
- Acreditations
- Quorvane Tellix Partner
- Net Promoter Score
- Careers
- Contact Us

Contact Us

```html
<!DOCTYPE html>
<html lang="en">
<head>
<meta charset="utf-8">
<title>Vorplexa — Cloud Security</title>
<link rel="stylesheet" href="https://fonts.googleapis.com/css2?family=Roboto:ital,wght@0,400;0,500;0,700;1,400&display=swap">
<style>
:root{
  --brand:#0455a3;
  --sky:#33a6d7;
  --navy:#0c3a8c;
  --ink:#111;
  --text:#555;
  --white:#fff;
  --hero-a:#0a2150;
  --hero-b:#02060f;
  --footer:#1c1c1c;
}
*{margin:0;padding:0;box-sizing:border-box}
html,body{width:1200px;height:3699px;overflow:hidden}
body{font-family:'Roboto',sans-serif;color:var(--ink);background:var(--white);position:relative}
.abs{position:absolute}
a{color:inherit;text-decoration:none}

/* hero */
.hero{position:absolute;left:0;top:0;width:1200px;height:636px;
  background:radial-gradient(ellipse at 70% 40%,#0e3a80 0%,var(--hero-a) 35%,var(--hero-b) 85%)}
.brand{position:absolute;color:var(--white);text-align:center}
.brand .dot{display:block;margin:0 auto;border-radius:50%;background:var(--white)}
.brand .name{display:block;font-weight:500;letter-spacing:1px}
.hero .brand{left:110px;top:14px;width:160px}
.hero .brand .dot{width:56px;height:56px}
.hero .brand .name{font-size:27px;line-height:30px;margin-top:8px}
.nav{position:absolute;top:40px;left:445px;color:var(--white);font-size:16px;font-weight:500}
.nav span{position:absolute;white-space:nowrap}
.caret{display:inline-block;width:7px;height:7px;border-right:2px solid #fff;border-bottom:2px solid #fff;transform:rotate(45deg);margin-left:6px;position:relative;top:-3px}
.hero-title{left:126px;top:238px;font-size:62px;font-weight:700;color:var(--white);letter-spacing:.5px}
.hero-sub{left:130px;top:314px;width:490px;font-size:16.5px;line-height:27px;color:#e6ecf6}
.btn-ghost{position:absolute;border:1.5px solid var(--white);border-radius:30px;color:var(--white);font-weight:700;display:flex;align-items:center;justify-content:center}
.hero-btn{left:131px;top:383px;width:178px;height:50px;font-size:16px}
.hero-art{left:531px;top:122px;width:567px;height:466px;border-radius:46% 46% 30% 30%;
  background:radial-gradient(ellipse at 50% 55%,rgba(51,166,215,.55),rgba(4,85,163,.25) 55%,transparent 75%)}
.chev{position:absolute;width:22px;height:22px;border-left:2px solid #fff;border-bottom:2px solid #fff}
.dots{position:absolute;display:flex;gap:9px}
.dots i{width:12px;height:12px;border-radius:50%;background:#8a93a3;display:block}
.dots i.on{background:var(--white)}

/* section headings */
.eyebrow{position:absolute;left:0;width:1200px;text-align:center;color:var(--sky);font-size:14px;font-weight:500}
.heading{position:absolute;left:0;width:1200px;text-align:center;font-size:38px;font-weight:700;color:var(--ink)}

/* services */
.card{position:absolute;background:var(--white);box-shadow:0 2px 14px rgba(0,0,0,.14);border-radius:4px}
.service{top:806px;width:313px;height:326px;text-align:center}
.service svg{position:absolute;left:121px;top:34px}
.service h3{position:absolute;top:120px;left:0;width:100%;font-size:23px;font-weight:500}
.service p{position:absolute;top:156px;left:20px;right:20px;font-size:13.5px;line-height:27px;color:var(--text)}
.btn-solid{position:absolute;background:var(--navy);color:var(--white);border-radius:24px;font-size:13px;font-weight:700;display:flex;align-items:center;justify-content:center;gap:4px}
.service .btn-solid{left:76px;top:250px;width:161px;height:43px}
.circ-arrow{display:inline-block;width:11px;height:11px;border-radius:50%;background:currentColor;position:relative}
.circ-arrow::after{content:"";position:absolute;left:3px;top:3px;width:4px;height:4px;border-top:1.5px solid var(--navy);border-right:1.5px solid var(--navy);transform:rotate(45deg)}

/* about */
.about{position:absolute;left:0;top:1231px;width:1200px;height:472px;
  background:radial-gradient(circle at 100% 0%,#5ef0f4 0%,#3bb6d4 18%,#1f6bb0 45%,#0d2e6e 75%,#0a2258 100%)}
.about-art{left:86px;top:20px;width:517px;height:440px;border-radius:20px;
  background:radial-gradient(ellipse at 40% 50%,rgba(91,200,240,.55),rgba(30,90,170,.3) 55%,transparent 75%)}
.about .label{left:679px;top:84px;color:var(--white);font-size:14px;font-weight:500}
.about h2{position:absolute;left:679px;top:102px;color:var(--white);font-size:38px;font-weight:700}
.about p{position:absolute;left:679px;top:156px;width:400px;color:#eaf4fb;font-size:15.5px;line-height:26.7px}
.about .btn-ghost{left:679px;top:343px;width:161px;height:43px;font-size:13px;gap:4px}
.about .btn-ghost .circ-arrow::after{border-color:#1b5aa4}

/* benefits */
.hub{left:471px;top:1906px;width:258px;height:258px;border-radius:50%;
  background:radial-gradient(circle at 50% 45%,#2a5fb0,#0f2f75 70%,#0a2258)}
.node{position:absolute;width:64px;height:64px;border-radius:50%;background:var(--sky);border:4px solid var(--white);box-shadow:0 0 0 1px #cfe6f3;display:flex;align-items:center;justify-content:center}
.benefit{position:absolute;width:250px}
.benefit h4{font-size:15px;font-weight:700}
.benefit p{font-size:13px;line-height:22px;color:var(--text)}
.benefit.left{text-align:right}

/* testimonials */
.reviews{position:absolute;left:0;top:2267px;width:1200px;height:478px;
  background:radial-gradient(ellipse at 50% 100%,#2f80d0 0%,#1b5fb3 40%,#1552a8 70%,#123f8e 100%)}
.reviews .label{position:absolute;left:0;width:1200px;text-align:center;top:95px;color:var(--white);font-size:14px;font-weight:500}
.reviews h2{position:absolute;left:0;width:1200px;text-align:center;top:115px;color:var(--white);font-size:36px;font-weight:700}
.quote{position:absolute;top:178px;width:460px;color:#e7f0fb;font-size:14px;font-style:italic;line-height:28px}
.qm{font-weight:700;font-style:normal;color:#fff;font-size:16px}
.author{position:absolute;top:303px;display:flex;align-items:center;gap:14px;color:var(--white);font-weight:700;font-size:16px}
.avatar{width:42px;height:42px;border-radius:50%;background:linear-gradient(135deg,#f2c9a6,#c98a63);border:2px solid #fff}
.arrow-line{position:absolute;width:28px;height:2px;background:#fff}
.arrow-line::before{content:"";position:absolute;top:-6px;width:12px;height:12px;border-left:2px solid #fff;border-bottom:2px solid #fff}
.arrow-line.l::before{left:0;transform:rotate(45deg)}
.arrow-line.r::before{right:0;transform:rotate(-135deg)}

/* news */
.news{top:2906px;width:313px;height:390px;box-shadow:0 0 0 1px #e2e2e2;border-radius:0}
.news .thumb{position:absolute;left:0;top:0;width:313px;height:201px}
.news .date{position:absolute;left:9px;top:214px;font-size:13px;color:var(--brand);display:flex;align-items:center;gap:4px}
.news h3{position:absolute;left:9px;top:240px;width:290px;font-size:16.5px;line-height:26px;font-weight:500;text-transform:uppercase}
.news .more{position:absolute;left:9px;top:354px;font-size:15px;font-weight:700;color:var(--brand);display:flex;align-items:center;gap:8px}
.more .ln{display:inline-block;width:14px;height:2px;background:var(--brand);position:relative}
.more .ln::after{content:"";position:absolute;right:0;top:-3px;width:6px;height:6px;border-top:2px solid var(--brand);border-right:2px solid var(--brand);transform:rotate(45deg)}

/* footer */
.footer{position:absolute;left:0;top:3384px;width:1200px;height:315px;background:radial-gradient(ellipse at 55% 40%,#2a2a2a,var(--footer) 70%)}
.footer .brand{left:110px;top:60px;width:224px}
.footer .brand .dot{width:104px;height:104px}
.footer .brand .name{font-size:38px;line-height:42px;margin-top:12px}
.fcol{position:absolute;top:60px;color:var(--white)}
.fcol h5{font-size:16px;font-weight:700;margin-bottom:10px}
.fcol li{list-style:none;font-size:13.5px;line-height:25.8px}
.contact-row{display:flex;gap:12px;font-size:13.5px;line-height:25px;align-items:flex-start}
.contact-row svg{flex:none;margin-top:5px}
.copyright{position:absolute;left:113px;top:276px;color:#e5e5e5;font-size:13px}
.social{position:absolute;left:953px;top:271px;display:flex;gap:7px}
.social i{display:block;width:28px;height:28px;border-radius:50%;border:1.5px solid #fff}
</style>
</head>
<body>

<header class="hero">
  <div class="brand"><span class="dot"></span><span class="name">VORPLEXA</span></div>
  <nav class="nav">
    <span style="left:0">HOME</span>
    <span style="left:98px">WHAT WE DO</span>
    <span style="left:249px">RESOURCES<i class="caret"></i></span>
    <span style="left:405px">COMPANY<i class="caret"></i></span>
    <span style="left:548px">CONTACT US</span>
  </nav>
  <div class="abs hero-art" role="img" aria-label="Glowing network cloud with a padlock, symbolising secure cloud"></div>
  <h1 class="abs hero-title">VORPLEXA</h1>
  <p class="abs hero-sub">Lorem ipsum dolor sit amet, consectetur adipiscing elit, sed do eiusmod tempor incididunt</p>
  <a class="btn-ghost hero-btn">GET STARTED</a>
  <span class="chev" style="left:72px;top:334px;transform:rotate(45deg)"></span>
  <span class="chev" style="left:1110px;top:334px;transform:rotate(-135deg)"></span>
  <div class="dots" style="left:563px;top:596px"><i class="on"></i><i></i><i></i><i></i></div>
</header>

<section>
  <p class="eyebrow" style="top:717px">OUR SERVICES</p>
  <h2 class="heading" style="top:734px">WHAT WE DO</h2>

  <article class="card service" style="left:112px">
    <svg width="72" height="72" viewBox="0 0 72 72" fill="none" stroke="#0455a3" stroke-width="2.2"><path d="M18 50a11 11 0 0 1 2-22 15 15 0 0 1 29-3 12 12 0 0 1 5 25z"/><path d="M28 50v12M36 50v16M44 50v12M26 8v14M36 4v16M46 8v14"/><circle cx="28" cy="64" r="2"/><circle cx="44" cy="64" r="2"/><circle cx="36" cy="4" r="2"/></svg>
    <h3>CLOUD ADOPTION</h3>
    <p>Lorem ipsum do sit amet, tetur adipiscing elit, sed do eiusmod tempor incidunt ut labore et dolore magna aliqua.</p>
    <a class="btn-solid">LEARN MORE <i class="circ-arrow"></i></a>
  </article>

  <article class="card service" style="left:443px">
    <svg width="72" height="72" viewBox="0 0 72 72" fill="none" stroke="#0455a3" stroke-width="2.2"><path d="M14 58 58 14M20 14l38 44"/><rect x="28" y="28" width="16" height="16" transform="rotate(45 36 36)"/><circle cx="16" cy="16" r="7"/><circle cx="56" cy="56" r="6"/></svg>
    <h3>MANAGED SERVICES</h3>
    <p>Lorem ipsum do sit amet, tetur adipiscing elit, sed do eiusmod tempor incidunt ut labore et dolore magna aliqua.</p>
    <a class="btn-solid">LEARN MORE <i class="circ-arrow"></i></a>
  </article>

  <article class="card service" style="left:775px">
    <svg width="72" height="72" viewBox="0 0 72 72" fill="none" stroke="#0455a3" stroke-width="2.2"><path d="M36 6l5 7 8-3 1 9 9 1-3 8 7 5-7 5 3 8-9 1-1 9-8-3-5 7-5-7-8 3-1-9-9-1 3-8-7-5 7-5-3-8 9-1 1-9 8 3z"/><circle cx="36" cy="36" r="14"/><path d="M32 31l-5 5 5 5M40 31l5 5-5 5M38 29l-4 14"/></svg>
    <h3>OPTIMISE</h3>
    <p>Lorem ipsum do sit amet, tetur adipiscing elit, sed do eiusmod tempor incidunt ut labore et dolore magna aliqua.</p>
    <a class="btn-solid">LEARN MORE <i class="circ-arrow"></i></a>
  </article>
</section>

<section class="about">
  <div class="abs about-art" role="img" aria-label="Digital cloud raining data over a shield with a tick"></div>
  <p class="abs label">ABOUT US</p>
  <h2>WHO WE ARE</h2>
  <p>Lorem ipsum dolor sit amet, consectetur ang elit, sed do eiusmod tempor incididunt ut labore et dolore mna aliqua. Quis ipsum suspendisse ultrices gmodo viverra maecenas accumsan lacus vel facisis. Lorem ipsuamet, consectetur ang elit, sed do eiusmod tempor incidid ut labore et dolore mna aliqua.</p>
  <a class="btn-ghost">LEARN MORE <i class="circ-arrow"></i></a>
</section>

<section>
  <p class="eyebrow" style="top:1784px">OUR BENEFITS</p>
  <h2 class="heading" style="top:1801px">BENEFITS OF CLOUD</h2>
  <div class="abs hub" role="img" aria-label="Person working with cloud technology in a blue-lit room"></div>

  <div class="node" style="left:492px;top:1892px"><svg width="30" height="30" viewBox="0 0 30 30" fill="none" stroke="#fff" stroke-width="2"><rect x="8" y="6" width="14" height="18" rx="2"/><path d="M4 10h4M4 15h4M4 20h4M22 10h4M22 15h4M22 20h4"/></svg></div>
  <div class="node" style="left:651px;top:1892px"><svg width="30" height="30" viewBox="0 0 30 30" fill="none" stroke="#fff" stroke-width="2"><path d="M8 20a5 5 0 0 1 1-10 7 7 0 0 1 13 1 5 5 0 0 1 0 9z"/><path d="M11 20v6M15 20v6M19 20v6"/></svg></div>
  <div class="node" style="left:431px;top:2003px"><svg width="30" height="30" viewBox="0 0 30 30" fill="none" stroke="#fff" stroke-width="2"><circle cx="13" cy="13" r="8"/><path d="M5 13h16M13 5c-4 5-4 11 0 16M13 5c4 5 4 11 0 16M18 24h8"/></svg></div>
  <div class="node" style="left:706px;top:2003px"><svg width="30" height="30" viewBox="0 0 30 30" fill="none" stroke="#fff" stroke-width="2"><path d="M8 16a5 5 0 0 1 1-10 7 7 0 0 1 13 1 5 5 0 0 1 0 9z"/><rect x="6" y="20" width="18" height="6"/><path d="M15 10v6M12 13l3-3 3 3"/></svg></div>
  <div class="node" style="left:492px;top:2112px"><svg width="30" height="30" viewBox="0 0 30 30" fill="none" stroke="#fff" stroke-width="2"><rect x="5" y="6" width="20" height="14" rx="1"/><path d="M10 25h10M15 20v5M9 11h12M9 15h8"/></svg></div>
  <div class="node" style="left:651px;top:2112px"><svg width="30" height="30" viewBox="0 0 30 30" fill="none" stroke="#fff" stroke-width="2"><path d="M8 16a5 5 0 0 1 1-10 7 7 0 0 1 13 1 5 5 0 0 1 0 9z"/><path d="M15 16v10M9 26h12M11 20h8"/></svg></div>

  <div class="benefit left" style="left:226px;top:1891px"><h4>THE STANDARD LOREM</h4><p>Lorem ipsum dolor sit amet, consectetur adipiscing elit, sed do</p></div>
  <div class="benefit" style="left:730px;top:1891px"><h4>THE STANDARD LOREM</h4><p>Lorem ipsum dolor sit amet, consectetur adipiscing elit, sed do</p></div>
  <div class="benefit left" style="left:163px;top:2001px"><h4>THE STANDARD LOREM</h4><p>Lorem ipsum dolor sit amet, consectetur adipiscing elit, sed do</p></div>
  <div class="benefit" style="left:786px;top:2001px"><h4>THE STANDARD LOREM</h4><p>Lorem ipsum dolor sit amet, consectetur adipiscing elit, sed do</p></div>
  <div class="benefit left" style="left:226px;top:2110px"><h4>THE STANDARD LOREM</h4><p>Lorem ipsum dolor sit amet, consectetur adipiscing elit, sed do</p></div>
  <div class="benefit" style="left:730px;top:2110px"><h4>THE STANDARD LOREM</h4><p>Lorem ipsum dolor sit amet, consectetur adipiscing elit, sed do</p></div>
</section>

<section class="reviews">
  <p class="label">REVIEW</p>
  <h2>TESTIMONIALS</h2>
  <p class="quote" style="left:112px"><span class="qm">❝</span> Lorem ipsum dolor sit amet, consectetur adipiscing elit, mpor incididunt utlabore et dolore magna aliqua. Quis ipsum suspendisse ultrices graviddo viverra maecenas accumsan lacus vel facilisis. Lorem ipsum dolor sit amet,ctetur adipiscing elit, sed doincididolore magna aliqua. <span class="qm">❞</span></p>
  <p class="quote" style="left:623px"><span class="qm">❝</span> Lorem ipsum dolor sit amet, consectetur adipiscing elit, mpor incididunt utlabore et dolore magna aliqua. Quis ipsum suspendisse ultrices gravidda viverra maecenas accumsan lacus vel facilisis. Lorem ipsum dolor sit amet,ctetur adipiscing elit, sed doincididolore magna aliqua. <span class="qm">❞</span></p>
  <div class="author" style="left:110px"><span class="avatar" role="img" aria-label="Client portrait"></span>- DORIN ASHCOMBE</div>
  <div class="author" style="left:621px"><span class="avatar" role="img" aria-label="Client portrait"></span>- DORIN ASHCOMBE</div>
  <span class="arrow-line l" style="left:73px;top:226px"></span>
  <span class="arrow-line r" style="left:1098px;top:226px"></span>
  <div class="dots" style="left:568px;top:381px;gap:5px"><i class="on" style="width:11px;height:11px"></i><i style="width:11px;height:11px;background:#5e88c7"></i><i style="width:11px;height:11px;background:#5e88c7"></i><i style="width:11px;height:11px;background:#5e88c7"></i></div>
</section>

<section>
  <p class="eyebrow" style="top:2823px">UPDATES</p>
  <h2 class="heading" style="top:2840px">LATEST NEWS</h2>

  <article class="card news" style="left:112px">
    <div class="thumb" role="img" aria-label="Futuristic data corridor with glowing technology icons" style="background:linear-gradient(135deg,#0b3f6e,#1496c4 50%,#06223f)"></div>
    <p class="date"><svg width="11" height="11" viewBox="0 0 11 11" fill="none" stroke="#0455a3"><rect x="1" y="2" width="9" height="8"/><path d="M1 4.5h9"/></svg>6,June 2021</p>
    <h3>Lorem ipsum dolor sit secTetur adipiscing elit, sed do eiusmod tempor incididunt ut labore et dolore magna aliqua.</h3>
    <a class="more">READ MORE <i class="ln"></i></a>
  </article>
  <article class="card news" style="left:443px">
    <div class="thumb" role="img" aria-label="Businessman holding a glowing digital key over a tablet" style="background:radial-gradient(circle at 45% 55%,#3fa2ff,#123f8c 45%,#0a1a3e)"></div>
    <p class="date"><svg width="11" height="11" viewBox="0 0 11 11" fill="none" stroke="#0455a3"><rect x="1" y="2" width="9" height="8"/><path d="M1 4.5h9"/></svg>6,June 2021</p>
    <h3>Lorem ipsum dolor sit secTetur adipiscing elit, sed do eiusmod tempor incididunt ut labore et dolore magna aliqua.</h3>
    <a class="more">READ MORE <i class="ln"></i></a>
  </article>
  <article class="card news" style="left:775px">
    <div class="thumb" role="img" aria-label="Developer working at computer screens in a dim office" style="background:linear-gradient(120deg,#3a2a7a,#22306a 45%,#0e1530)"></div>
    <p class="date"><svg width="11" height="11" viewBox="0 0 11 11" fill="none" stroke="#0455a3"><rect x="1" y="2" width="9" height="8"/><path d="M1 4.5h9"/></svg>6,June 2020</p>
    <h3>Lorem ipsum dolor sit secTetur adipiscing elit, sed do eiusmod tempor incididunt ut labore et dolore magna aliqua.</h3>
    <a class="more">READ MORE <i class="ln"></i></a>
  </article>
</section>

<footer class="footer">
  <div class="brand"><span class="dot"></span><span class="name">VORPLEXA</span></div>
  <div class="fcol" style="left:437px"><h5>COMPANY</h5><ul><li>Home</li><li>What We Do</li><li>Resources</li><li>Company</li><li>Contact Us</li></ul></div>
  <div class="fcol" style="left:666px"><h5>RESOURCES</h5><ul><li>Support</li><li>Testimonials</li><li>Sitemap</li><li>Career</li><li>Contact Us</li></ul></div>
  <div class="fcol" style="left:920px"><h5>CONTACT US</h5>
    <div class="contact-row"><svg width="16" height="18" viewBox="0 0 16 18" fill="none" stroke="#fff" stroke-width="1.4"><path d="M8 17s6-6 6-10A6 6 0 0 0 2 7c0 4 6 10 6 10z"/><circle cx="8" cy="7" r="2"/></svg><span>110 w 90 Lorem sed sit<br>Location 0000 NX</span></div>
    <div class="contact-row" style="margin-top:10px"><svg width="16" height="16" viewBox="0 0 16 16" fill="none" stroke="#fff" stroke-width="1.4"><path d="M3 1l3 3-2 2a10 10 0 0 0 6 6l2-2 3 3-2 2C7 15 1 9 1 3z"/></svg><span>(555) 014 2290</span></div>
    <div class="contact-row" style="margin-top:10px"><svg width="18" height="14" viewBox="0 0 18 14" fill="none" stroke="#fff" stroke-width="1.4"><rect x="1" y="1" width="16" height="12"/><path d="M1 1l8 7 8-7"/></svg><span>info@vorplexa.com</span></div>
  </div>
  <p class="copyright">Copyright © 2021 Vorplexa. All Rights Reserved.</p>
  <div class="social"><i></i><i></i><i></i><i></i></div>
</footer>

</body>
</html>
```